Home Remodeling company needs a business card design

we need a business card design for home remodeling company in hamilton county, indiana USA. we offers a wide range of construction services including whole house renovations, Design and Build Basements and Kitchen and Bathroom Remodeling . we would like to see designs for both site of business card that use the same color of the company logo and also including all information below :
1- Karim Feltous CEO / General Contractor
2- all company contacts Telephone numbers ( 1-888-DULOM-47 ) ( 317-555-0193) email address ( info@dulomhome.com) website ( www.dulomhome.com ) and social media logos (Facebook- twitter- google plus )
3- company logo
4- licensed . insured . bonded

```html
<!DOCTYPE html>
<html lang="en">
<head>
<meta charset="utf-8">
<title>Dulom Home Remodeling – Business Card</title>
<link rel="stylesheet" href="https://fonts.googleapis.com/css2?family=Montserrat:wght@600;800&family=Arimo:wght@400&family=Source+Sans+3:wght@400&display=swap">
<style>
  :root {
    --brand-red: #c8323a;
    --brand-dark: #3a3a3c;
    --brand-grey: #808083;
    --paper: #ffffff;
    --backdrop: #e4e4e4;
    --social-1: #4a4a4d;
    --social-2: #8a8a8e;
    --social-3: #c8323a;
  }
  * { margin: 0; padding: 0; box-sizing: border-box; }
  html, body {
    width: 1189px;
    height: 1200px;
    overflow: hidden;
    background: var(--backdrop);
  }
  .canvas {
    position: relative;
    width: 1189px;
    height: 1200px;
  }
  .card {
    position: absolute;
    left: 114px;
    width: 960px;
    height: 548px;
    background: var(--paper);
    box-shadow: 0 4px 14px rgba(0,0,0,0.18);
    display: block;
  }
  .card--front { top: 27px; }
  .card--back { top: 625px; }
  .wordmark {
    font-family: "Montserrat", sans-serif;
    font-weight: 800;
    fill: var(--brand-dark);
  }
  .wordmark-mark { fill: var(--brand-red); }
  .descriptor {
    font-family: "Montserrat", sans-serif;
    font-weight: 600;
    fill: var(--brand-grey);
  }
  .credentials {
    font-family: "Source Sans 3", sans-serif;
    font-weight: 400;
    font-size: 37px;
    fill: var(--brand-dark);
  }
  .red-panel { fill: var(--brand-red); }
  .swoosh { fill: var(--brand-dark); }
  .divider { stroke: var(--paper); stroke-width: 1.5; opacity: 0.85; }
  .person-name, .person-role, .contact-line {
    font-family: "Arimo", sans-serif;
    font-weight: 400;
    fill: var(--paper);
  }
  .person-name { font-size: 38px; }
  .person-role { font-size: 25px; }
  .contact-line { font-size: 25px; }
  .contact-icon-bg { fill: var(--paper); }
  .contact-icon-glyph { fill: var(--brand-red); }
  .contact-icon-stroke { fill: none; stroke: var(--brand-red); stroke-width: 1.6; }
  .social-tile-1 { fill: var(--social-1); }
  .social-tile-2 { fill: var(--social-2); }
  .social-tile-3 { fill: var(--social-3); }
</style>
</head>
<body>
<main class="canvas">

  <!-- Front side -->
  <svg class="card card--front" viewBox="0 0 960 548" aria-label="Business card front">
    <rect class="wordmark-mark" x="126" y="102" width="30" height="30"/>
    <text class="wordmark" x="172" y="167" font-size="134" textLength="664" lengthAdjust="spacing">DULOM</text>
    <text class="descriptor" x="172" y="218" font-size="38" textLength="664" lengthAdjust="spacing">HOME REMODELING</text>

    <path class="red-panel" d="M0 180 Q480 460 960 180 L960 548 L0 548 Z"/>
    <path class="swoosh" d="M33 200 Q480 390 913 204 Q480 420 33 200 Z"/>
    <text class="credentials" x="480" y="261" text-anchor="middle">licensed . insured . bonded</text>

    <text class="person-name" x="251" y="407" text-anchor="middle">Karim Feltous</text>
    <text class="person-role" x="251" y="447" text-anchor="middle">CEO / General Contractor</text>

    <line class="divider" x1="469" y1="342" x2="469" y2="493"/>

    <g class="contact-icon" transform="translate(527,360)">
      <rect class="contact-icon-bg" width="20" height="20" rx="2"/>
      <path class="contact-icon-glyph" d="M4 7 Q10 2 16 7 L15 9 L12 8 L12 7 Q10 6 8 7 L8 8 L5 9 Z M6 10 H14 L15 16 H5 Z"/>
    </g>
    <text class="contact-line" x="568" y="376">317-555-0193</text>

    <g class="contact-icon" transform="translate(527,392)">
      <rect class="contact-icon-bg" width="20" height="20" rx="2"/>
      <path class="contact-icon-glyph" d="M4 7 Q10 2 16 7 L15 9 L12 8 L12 7 Q10 6 8 7 L8 8 L5 9 Z M6 10 H14 L15 16 H5 Z"/>
    </g>
    <text class="contact-line" x="568" y="408">1-888-DULOM-47</text>

    <g class="contact-icon" transform="translate(527,426)">
      <rect class="contact-icon-bg" width="20" height="20" rx="2"/>
      <circle class="contact-icon-stroke" cx="10" cy="10" r="6"/>
      <path class="contact-icon-stroke" d="M4 10 H16 M10 4 Q6 10 10 16 M10 4 Q14 10 10 16"/>
    </g>
    <text class="contact-line" x="568" y="442">www.dulomhome.com</text>

    <g class="contact-icon" transform="translate(527,460)">
      <rect class="contact-icon-bg" width="20" height="20" rx="2"/>
      <rect class="contact-icon-stroke" x="4" y="6" width="12" height="9"/>
      <path class="contact-icon-stroke" d="M4 6 L10 11 L16 6"/>
    </g>
    <text class="contact-line" x="568" y="476">info@dulomhome.com</text>
  </svg>

  <!-- Back side -->
  <svg class="card card--back" viewBox="0 0 960 548" aria-label="Business card back">
    <rect class="wordmark-mark" x="116" y="192" width="32" height="32"/>
    <text class="wordmark" x="164" y="262" font-size="138" textLength="684" lengthAdjust="spacing">DULOM</text>
    <text class="descriptor" x="164" y="313" font-size="39" textLength="684" lengthAdjust="spacing">HOME REMODELING</text>

    <g class="social-links" role="img" aria-label="Social media profile links">
      <rect class="social-tile-1" x="328" y="375" width="88" height="94" rx="8"/>
      <rect class="social-tile-2" x="435" y="375" width="88" height="94" rx="8"/>
      <rect class="social-tile-3" x="542" y="375" width="88" height="94" rx="8"/>
    </g>
  </svg>

</main>
</body>
</html>
```